Website for "Bright Morrow Ltd" cleaning bsuiness

We require a website to expose our business to the local market. We want to provide background on who we are and what we do but in an easily digestible way. We clean domestic and commercial premises and want to provide a list of all of our services to potential customers. We operate out of Warrington in the UK.

We would like the website to be animated in some way so that the experience of using it is not dull or mundane. This website needs to be an extension of our company.

Target Market(s)

30 - 60 year olds for Domestic plus commercial clients

Industry/Entity Type

Cleaning Service

Coding

Coded - Design and coding required

Number of Pages Required

4 page

Font styles to use
Sans Serif

Colors
0455a3
3176b5
85acd3
cfdeed
ffffff
000000
1b1b1b
c8c8c8
757575

Requirements
Must have
• Logo which has been provided. Theme based around the logo and its colours. Simple layout to avoid confusion.
Nice to have
• Animations where possible to impress the customer.
Should not have
• any pictures of cleaning equipment, fairies, maids etc

```html
<!DOCTYPE html>
<html lang="en">
<head>
<meta charset="utf-8">
<title>Bright Morrow Ltd – Professional Cleaning Service</title>
<link rel="stylesheet" href="https://fonts.googleapis.com/css2?family=Lato:wght@400;900&family=PT+Sans:wght@400;700&family=Raleway:wght@400;500&display=swap">
<style>
:root{
  --navy:#14279a;
  --navy-deep:#0f1b5e;
  --heading:#1b2e9e;
  --accent:#2f7fe6;
  --sky-1:#cfe2fb;
  --sky-2:#8fbdf0;
  --pale:#e2e8f8;
  --text:#333333;
  --muted:#757575;
  --light:#c8c8c8;
  --white:#ffffff;
}
*{box-sizing:border-box;margin:0;padding:0}
html,body{width:1200px;height:2956px;overflow:hidden;background:var(--white)}
body{font-family:"PT Sans",sans-serif;color:var(--text)}
.canvas{position:relative;width:1200px;height:2956px;overflow:hidden}
.abs{position:absolute}

/* hero */
.hero{left:0;top:0;width:1200px;height:627px;background:linear-gradient(135deg,#e6f0fd 0%,var(--sky-1) 35%,var(--sky-2) 100%)}
.hero-sheen{left:0;top:0;width:1200px;height:627px;background:linear-gradient(115deg,rgba(255,255,255,.35) 0 30%,rgba(255,255,255,0) 30%)}
.nav-plate{left:0;top:0;width:1200px;height:140px;background:rgba(255,255,255,.92);clip-path:polygon(0 0,100% 0,100% 40%,68% 40%,50% 100%,32% 40%,0 40%)}
.nav{left:0;top:42px;width:1200px;font-family:"PT Sans",sans-serif;font-size:18px;color:#333}
.nav span{position:absolute;top:0;transform:translateX(-50%);letter-spacing:.3px}
.nav .active{color:var(--accent)}
.brand{left:450px;top:28px;width:300px;text-align:center;font-family:"PT Sans",sans-serif;font-weight:700;font-size:32px;color:var(--heading);line-height:1}
.brand small{display:block;font-size:14px;font-weight:700;margin-top:6px;letter-spacing:.5px}
.hero-title{left:79px;top:240px;font-family:"Lato",sans-serif;font-weight:900;font-size:70px;color:var(--heading);letter-spacing:.5px}
.hero-sub{left:79px;top:330px;font-family:"PT Sans",sans-serif;font-size:42px;line-height:49px;color:#1f2a4a}
.btn-quote{left:79px;top:465px;width:154px;height:43px;background:var(--navy);color:var(--white);font-size:21px;display:flex;align-items:center;justify-content:center;border-radius:3px}
.hero-photo{left:522px;top:256px;width:678px;height:371px;background:radial-gradient(ellipse at 60% 60%,#f3d9c8 0%,#c6d7ee 55%,rgba(143,189,240,0) 80%)}

/* info band */
.info{left:0;top:627px;width:1200px;height:201px;background:var(--navy);clip-path:polygon(0 0,100% 0,100% 58.7%,50% 100%,0 58.7%)}
.info-item{top:672px;display:flex;gap:18px;align-items:flex-start;color:var(--white);font-size:20px;line-height:29px}
.info-item svg{margin-top:2px}
.info-divider{top:668px;width:1px;height:72px;background:rgba(255,255,255,.35)}

/* welcome */
.eyebrow{left:0;width:1200px;text-align:center;font-size:15px;letter-spacing:.5px;color:#222}
.section-title{left:0;width:1200px;text-align:center;font-family:"Raleway",sans-serif;font-size:41px;color:var(--heading)}
.section-title .hl{color:var(--accent)}
.intro{left:207px;top:958px;width:786px;text-align:center;font-size:14.5px;line-height:24px;color:var(--muted)}
.intro-shadow{left:200px;top:1072px;width:800px;height:18px;background:radial-gradient(ellipse at 50% 0,rgba(0,0,0,.12),rgba(0,0,0,0) 70%)}

/* services wheel */
.wheel{left:394px;top:1202px;width:406px;height:406px;border-radius:50%;background:radial-gradient(circle at 50% 45%,#2b3c66 0%,#15203f 70%,#0e1630 100%)}
.wheel-brand{left:394px;top:1360px;width:406px;text-align:center;font-family:"PT Sans",sans-serif;font-weight:700;font-size:44px;color:var(--white);line-height:1.05}
.thumb{width:126px;height:126px;border-radius:50%;border:4px solid var(--white);box-shadow:0 2px 6px rgba(0,0,0,.25)}
.svc{width:260px;font-size:14.5px;line-height:25px;color:var(--muted)}
.svc h3{font-family:"PT Sans",sans-serif;font-weight:400;font-size:21px;color:#222;margin-bottom:5px}
.svc .more{display:inline-block;margin-top:3px;color:var(--navy);font-size:15px}
.svc.left{text-align:right}
.svc.right{text-align:left}

/* newsletter */
.news-band{left:0;top:1688px;width:1200px;height:202px;background:var(--pale);clip-path:polygon(0 0,100% 0,100% 56.4%,50% 100%,0 56.4%)}
.dark{left:0;top:1802px;width:1200px;height:582px;background:var(--navy-deep);clip-path:polygon(0 0,50% 15.1%,100% 0,100% 84.7%,50% 100%,0 84.7%)}
.news-eyebrow{left:0;top:1718px;width:1200px;text-align:center;font-size:15px;color:var(--navy);letter-spacing:.3px}
.news-title{left:0;top:1733px;width:1200px;text-align:center;font-family:"Raleway",sans-serif;font-size:42px;color:var(--accent)}
.news-input{left:300px;top:1791px;width:429px;height:45px;background:#eef1f9;border:1px solid #d4dbee;display:flex;align-items:center;padding-left:16px;gap:16px;font-size:14px;color:#666}
.news-submit{left:743px;top:1791px;width:157px;height:45px;background:var(--navy);color:var(--white);font-size:20px;display:flex;align-items:center;justify-content:center}

/* service cards */
.dark-eyebrow{left:0;top:1948px;width:1200px;text-align:center;font-size:15px;color:var(--white);letter-spacing:.3px}
.dark-title{left:0;top:1962px;width:1200px;text-align:center;font-family:"Raleway",sans-serif;font-size:42px;color:var(--white)}
.dark-title .hl{color:var(--accent)}
.card{top:2043px;height:236px;border:1px solid rgba(255,255,255,.55)}
.card-img{width:100%;height:134px}
.card-body{padding:10px 8px 0;text-align:center;font-size:14.5px;line-height:23px;color:#c8d0ee}
.card-body h4{font-family:"PT Sans",sans-serif;font-weight:400;font-size:17px;color:#7fb2f5;margin-bottom:2px}
.card-body h4.white{color:var(--white)}
.card.featured{border:3px solid #c8c8c8;background:linear-gradient(160deg,#fbf3e6,#e7e1d6 60%,#d8d2c8)}
.featured-text{position:absolute;left:0;top:58px;width:100%;text-align:center;font-size:21px;line-height:24px;color:#111;padding:0 26px}
.featured-link{position:absolute;left:0;top:162px;width:100%;text-align:center;font-size:20px;color:#111;text-decoration:underline}
.arrow{top:2130px}

/* testimonial */
.quote-mark{left:0;top:2520px;width:1200px;text-align:center;font-family:"Lato",sans-serif;font-weight:900;font-size:60px;line-height:60px;color:#b9b9b9}
.testimonial{left:250px;top:2578px;width:700px;text-align:center;font-size:15.5px;line-height:26px;color:#9a9a9a}
.client{left:0;top:2674px;width:1200px;text-align:center;font-size:15.5px;color:#333}
.dots{left:562px;top:2713px;display:flex;gap:10px}
.dots i{width:11px;height:11px;border-radius:50%;border:1.5px solid var(--navy)}
.dots i.on{background:var(--navy)}

/* footer */
.footer{left:0;top:2620px;width:1200px;height:336px;background:linear-gradient(180deg,#2a4fb0 0%,#1f3c98 45%,#1b3489 100%)}
.footer-haze{left:0;top:2620px;width:1200px;height:336px;background:radial-gradient(ellipse at 15% 20%,rgba(150,190,255,.35),rgba(150,190,255,0) 50%),radial-gradient(ellipse at 85% 30%,rgba(120,170,255,.3),rgba(120,170,255,0) 50%)}
.footer-notch{left:0;top:2619px;width:1200px;height:130px;background:var(--white);clip-path:polygon(0 0,100% 0,50% 100%)}
.social{top:2795px;display:flex;gap:45px;left:494px}
.social i{width:18px;height:18px;border-radius:50%;border:2px solid var(--white)}
.foot-links{left:0;top:2856px;width:1200px;font-size:15px;color:var(--white)}
.foot-links span{position:absolute;transform:translateX(-50%)}
.foot-rule{left:187px;top:2898px;width:826px;height:1px;background:rgba(255,255,255,.45)}
.copyright{left:0;top:2917px;width:1200px;text-align:center;font-size:15px;color:var(--white)}
.footer-photo{left:926px;top:2748px;width:274px;height:208px;background:radial-gradient(ellipse at 55% 55%,#f1d6c2 0%,#d9b9a6 35%,rgba(40,70,160,0) 75%)}
</style>
</head>
<body>
<div class="canvas">

  <!-- hero -->
  <div class="abs hero"></div>
  <div class="abs hero-sheen"></div>
  <div class="abs hero-photo" role="img" aria-label="Photo of two smiling cleaners holding cleaning supplies"></div>
  <div class="abs nav-plate"></div>
  <nav class="abs nav">
    <span class="active" style="left:106px">HOME</span>
    <span style="left:270px">ABOUT</span>
    <span style="left:441px">SERVICES</span>
    <span style="left:794px">GALLERY</span>
    <span style="left:906px">BLOGS</span>
    <span style="left:1082px">CONTACT</span>
  </nav>
  <div class="abs brand">Bright Morrow<small>Ltd</small></div>
  <h1 class="abs hero-title">CLEAN HOME</h1>
  <p class="abs hero-sub">PROFESSIONAL SERVICE,<br>FAIR PRICE.</p>
  <div class="abs btn-quote">QUICK QUOTE</div>

  <!-- info band -->
  <div class="abs info"></div>
  <div class="abs info-item" style="left:80px">
    <svg width="54" height="54" viewBox="0 0 24 24" fill="none" stroke="#fff" stroke-width="1.3" stroke-linejoin="round"><path d="M5 3h4l2 5-2.5 1.5a11 11 0 0 0 6 6L16 13l5 2v4a2 2 0 0 1-2 2A17 17 0 0 1 3 5a2 2 0 0 1 2-2z"/></svg>
    <div>Have A Question?<br>123 456 7878</div>
  </div>
  <div class="abs info-divider" style="left:380px"></div>
  <div class="abs info-item" style="left:456px">
    <svg width="46" height="52" viewBox="0 0 24 26" fill="none" stroke="#fff" stroke-width="2"><circle cx="12" cy="15" r="9"/><path d="M9 2h6M12 2v4M12 15V10M12 15l3 2"/></svg>
    <div>We are Open Mon-Fri<br>9:00 a.m To 8:00 p.m</div>
  </div>
  <div class="abs info-divider" style="left:758px"></div>
  <div class="abs info-item" style="left:820px">
    <svg width="56" height="40" viewBox="0 0 28 20" fill="none" stroke="#fff" stroke-width="1.4"><rect x="1" y="1" width="26" height="18"/><path d="M1 1l13 10L27 1M1 19l9-9M27 19l-9-9"/></svg>
    <div>Need Support<br><span style="font-size:17px">hello@brightmorrow.co</span></div>
  </div>

  <!-- welcome -->
  <div class="abs eyebrow" style="top:871px">WELCOME TO OUR SITE</div>
  <h2 class="abs section-title" style="top:886px">Professional Cleaning Service <span class="hl">Company</span></h2>
  <p class="abs intro">Lorem Ipsum is simply dummy text of the printing and typesetting industry. Lorem Ipsum has been the industry's standard dummy text ever since the 1500s, when an unknown printer took a galley of type and scrambled it to make a type specimen book.It has survived not only five centuries, but also the leap into electronic typesetting, remaining essentially unchanged.</p>
  <div class="abs intro-shadow"></div>

  <!-- services wheel -->
  <div class="abs wheel" role="img" aria-label="Photo of the cleaning team in uniform"></div>
  <div class="abs wheel-brand">Bright<br>Morrow</div>

  <div class="abs thumb" style="left:435px;top:1145px;background:linear-gradient(150deg,#e8eef3,#9fb1bf)" role="img" aria-label="Photo of commercial window cleaning"></div>
  <div class="abs thumb" style="left:660px;top:1145px;background:linear-gradient(150deg,#eef0f2,#8d9eb2)" role="img" aria-label="Photo of desk polishing"></div>
  <div class="abs thumb" style="left:331px;top:1332px;background:linear-gradient(150deg,#f2ece4,#b29f88)" role="img" aria-label="Photo of contract daily cleaning"></div>
  <div class="abs thumb" style="left:741px;top:1332px;background:linear-gradient(150deg,#c9d3b8,#6d7f5a)" role="img" aria-label="Photo of a bin being emptied"></div>
  <div class="abs thumb" style="left:445px;top:1497px;background:linear-gradient(150deg,#f0eeec,#b8b0a8)" role="img" aria-label="Photo of vacuuming a carpet"></div>
  <div class="abs thumb" style="left:650px;top:1497px;background:linear-gradient(150deg,#f7f7f7,#a9adb2)" role="img" aria-label="Photo of a clean toilet"></div>

  <div class="abs svc left" style="left:162px;top:1135px">
    <h3>Commercial cleaning</h3>
    Lorem Ipsum is simply dummy text of the printing and typesetting industry.<br><span class="more">READMORE »</span>
  </div>
  <div class="abs svc left" style="left:60px;top:1335px">
    <h3>Contract daily cleaning</h3>
    Lorem Ipsum is simply dummy text of the printing and<br><span class="more">READMORE »</span>
  </div>
  <div class="abs svc left" style="left:165px;top:1522px">
    <h3>Vacuuming</h3>
    Lorem Ipsum is simply dummy text of the printing and typesetting industry.<br><span class="more">READMORE »</span>
  </div>
  <div class="abs svc right" style="left:798px;top:1135px">
    <h3>Desk polishing</h3>
    Lorem Ipsum is simply dummy text of the printing and typesetting industry.<br><span class="more">READMORE »</span>
  </div>
  <div class="abs svc right" style="left:885px;top:1335px">
    <h3>Bin emptying</h3>
    Lorem Ipsum is simply dummy text of the printing and<br><span class="more">READMORE »</span>
  </div>
  <div class="abs svc right" style="left:788px;top:1522px">
    <h3>Toilet cleaning</h3>
    Lorem Ipsum is simply dummy text of the printing and typesetting industry.<br><span class="more">READMORE »</span>
  </div>

  <!-- newsletter + dark services -->
  <div class="abs dark"></div>
  <div class="abs news-band"></div>
  <div class="abs news-eyebrow">INTRESTED IN OUR WORK?</div>
  <h2 class="abs news-title">Newsletter</h2>
  <div class="abs news-input">
    <svg width="22" height="16" viewBox="0 0 22 16"><rect width="22" height="16" fill="#9aa3b8"/><path d="M0 0l11 8 11-8" fill="none" stroke="#eef1f9" stroke-width="1.5"/></svg>
    Enter Email
  </div>
  <div class="abs news-submit">SUBMIT</div>

  <div class="abs dark-eyebrow">OUR SERVICES</div>
  <h2 class="abs dark-title">Superior <span class="hl">Clining Solution</span></h2>

  <svg class="abs arrow" style="left:26px" width="20" height="54" viewBox="0 0 20 54"><path d="M18 2L3 27l15 25" fill="none" stroke="#c8c8c8" stroke-width="2"/></svg>
  <svg class="abs arrow" style="left:1154px" width="20" height="54" viewBox="0 0 20 54"><path d="M2 2l15 25L2 52" fill="none" stroke="#c8c8c8" stroke-width="2"/></svg>

  <div class="abs card featured" style="left:75px;width:238px" role="img" aria-label="Photo of a cleaner with supplies behind a white overlay">
    <div class="featured-text">Weekly, fotnightly, monthly and adhoc cleans available</div>
    <div class="featured-link">READ MORE</div>
  </div>
  <div class="abs card" style="left:349px;width:232px">
    <div class="card-img" style="background:linear-gradient(160deg,#f4f1ec,#c9c0b3)" role="img" aria-label="Photo of carpet cleaning"></div>
    <div class="card-body"><h4 class="white">Carpet Cleaning</h4>Lorem Ipsum is simply dummy text of the printing...</div>
  </div>
  <div class="abs card" style="left:619px;width:234px">
    <div class="card-img" style="background:linear-gradient(160deg,#f3e9f0,#b6a2c6)" role="img" aria-label="Photo of ironing clothes"></div>
    <div class="card-body"><h4>Ironing</h4>Lorem Ipsum is simply dummy text of the printing...</div>
  </div>
  <div class="abs card" style="left:889px;width:234px">
    <div class="card-img" style="background:linear-gradient(160deg,#cfd6dc,#7f8e9a)" role="img" aria-label="Photo of a steam cleaner on a tiled floor"></div>
    <div class="card-body"><h4>Tiled floor steam clean</h4>Lorem Ipsum is simply dummy text of the printing...</div>
  </div>

  <!-- testimonial -->
  <div class="abs footer" role="img" aria-label="Blurred photo of a bright blue interior"></div>
  <div class="abs footer-haze"></div>
  <div class="abs footer-notch"></div>

  <div class="abs eyebrow" style="top:2434px">TESTIMONIAL</div>
  <h2 class="abs section-title" style="top:2448px">What Our <span class="hl">Client Say</span></h2>
  <div class="abs quote-mark">“</div>
  <p class="abs testimonial">Lorem Ipsum is simply dummy text of the printing and typesetting industry. Lorem Ipsum has been the industry's standard dummy text ever since the 1500s, when an unknown printer took a galley of type and scrambled it to make a type specimen book.</p>
  <div class="abs client">- Client Name</div>
  <div class="abs dots"><i class="on"></i><i></i><i></i><i></i></div>

  <!-- footer -->
  <div class="abs social"><i></i><i></i><i></i><i></i></div>
  <div class="abs foot-links">
    <span style="left:398px">Home</span>
    <span style="left:492px">About</span>
    <span style="left:593px">Services</span>
    <span style="left:697px">Blogs</span>
    <span style="left:794px">Contact</span>
  </div>
  <div class="abs foot-rule"></div>
  <div class="abs copyright">© <b>Bright Morrow</b> - 2016 All Right Reserved</div>
  <div class="abs footer-photo" role="img" aria-label="Photo of a smiling cleaner holding a spray bottle and bucket"></div>

</div>
</body>
</html>
```